Catalogue Design Project

We need a catalog design for a new private university called Redwell Institute Bayshore (see website www.rwi-bs.org). The catalog should be about 30 pages maximum and will include items such as General Information, Academic schedule, department descriptions, program descriptions, course descriptions, school policies, student services, admissions, San diego Lifestyle, etc.
I will provide the text but I need a professional design with regard to page layouts. I have provided some examples.
Ok, i posted the catalog content, just missing course descriptions.
Target Market(s)
Young Professionals, Foreign Students
Industry/Entity Type
University
Look and feel
Each slider illustrates characteristics of the customer's brand and the style your logo design should communicate.

```html
<!DOCTYPE html>
<html lang="en">
<head>
<meta charset="utf-8">
<title>Student Services – Redwell Institute Bayshore</title>
<link rel="stylesheet" href="https://fonts.googleapis.com/css2?family=Carlito:wght@400;700&display=swap">
<style>
  :root {
    --brand-blue: #2f67a8;
    --brand-blue-dark: #23548e;
    --rule-blue: #5b86b8;
    --text: #1a1a1a;
    --muted: #8a8f96;
    --paper: #ffffff;
    --photo-light: #eef1f4;
    --photo-mid: #c9ced4;
    --dots: #d5d9de;
  }
  * { margin: 0; padding: 0; box-sizing: border-box; }
  html, body { width: 927px; height: 1200px; overflow: hidden; background: var(--paper); }
  .page {
    position: relative;
    width: 927px;
    height: 1200px;
    font-family: "Carlito", "Calibri", sans-serif;
    color: var(--text);
    overflow: hidden;
  }
  .header-art { position: absolute; left: 0; top: 0; width: 927px; height: 150px; }
  .dot-mark {
    position: absolute; left: 58px; top: 34px; width: 158px; height: 36px;
    background: var(--dots); border-radius: 18px;
  }
  .header-photo {
    position: absolute; left: 606px; top: 0; width: 321px; height: 103px;
    background: linear-gradient(90deg, var(--paper) 0%, var(--photo-light) 35%, var(--photo-mid) 100%);
  }
  .section-tab {
    position: absolute; right: 0; top: 103px; width: 344px; height: 41px;
    display: flex; align-items: center; justify-content: flex-end;
    padding-right: 16px;
    color: #fff; font-size: 29px; letter-spacing: 0.3px;
  }
  .content {
    position: absolute; left: 79px; top: 180px; width: 770px;
    font-size: 17.6px; line-height: 26.5px;
  }
  .page-title {
    text-align: center; font-weight: 700; font-size: 24.5px; line-height: 30px;
    margin-bottom: 19px;
  }
  .service { margin-bottom: 26.5px; }
  .service h2 {
    font-size: 17.6px; font-weight: 400; text-decoration: underline;
    line-height: 26.5px;
  }
  .service p { text-align: justify; }
  .footer-rule {
    position: absolute; left: 0; top: 1155px; width: 927px; height: 2px;
    background: var(--rule-blue);
  }
  .folio {
    position: absolute; right: 36px; top: 1171px;
    font-size: 12.5px; color: var(--muted); letter-spacing: 0.3px;
  }
</style>
</head>
<body>
<div class="page">
  <svg class="header-art" viewBox="0 0 927 150" aria-hidden="true">
    <rect x="0" y="102" width="927" height="2" fill="var(--rule-blue)"/>
    <polygon points="606,103 927,103 927,144 583,144" fill="var(--brand-blue)"/>
    <rect x="583" y="142" width="344" height="2" fill="var(--brand-blue-dark)"/>
  </svg>
  <div class="dot-mark" role="img" aria-label="Decorative dot pattern in blue and grey"></div>
  <div class="header-photo" role="img" aria-label="Faded photograph of a student leaping"></div>
  <div class="section-tab">STUDENT SERVICES</div>

  <main class="content">
    <h1 class="page-title">Student Services</h1>

    <section class="service">
      <h2>Tutoring</h2>
      <p>In order to ensure all students are keeping on task with their studies, Redwell Institute provides free weekly tutoring for most courses offered. Our goal is to ensure students graduate with all knowledge needed for their future success. Please see the information desk for our current tutoring schedule.</p>
    </section>

    <section class="service">
      <h2>Student Activities</h2>
      <p>Once a month, RWIB will arrange for an off-campus activity relating to students’ coursework. Trips can include tours of nearby businesses, schools and job placement centers. The university will also occasionally take students on trips to local recreational sites such as Mission Bay, Coronado, Balboa Park, and the Bayside Zoo.</p>
    </section>

    <section class="service">
      <h2>Transportation</h2>
      <p>In addition to providing local bus and trolley maps, train timetables, and general San Diego maps, we are more than willing to help students with directions to and from our university. Our campus is very centrally located in the downtown financial district. The Civic College trolley stop, several city bus lines, access to freeways 5, 163, and 94 are all less than 5 minutes away. Major shopping and dining areas such as Marlow Plaza and Pier Row Village are also nearby, as well as the San Diego International Airport and the Coastline Rail Station.</p>
    </section>

    <section class="service">
      <h2>Housing</h2>
      <p>San Diego is a popular, fast-growing destination for foreign students, so short/long term student housing is easily available. Students in need of housing need look no further than our information desk. We contract with several dormitories and can place you with a quick turnaround. We also aid in finding nearby apartments, shared rooms, and homestay options for out-of-state or international students.</p>
    </section>

    <section class="service">
      <h2>Health Insurance</h2>
      <p>Students needing affordable health insurance can pick up pamphlets from several providers – these are available at the information desk.</p>
    </section>
  </main>

  <div class="footer-rule"></div>
  <div class="folio">21::: REDWELL INSTITUTE</div>
</div>
</body>
</html>
```